Business card for law firm

Need business card for new law firm. Think confident, authoritative, conservative, but not stuffy or old-fashioned.

Contact Information for Business Card

Content for card - logo (uploaded), plus the following:

Paul Whitcombe (larger font)
Managing Partner (larger font, but not as large as name)
Level 9, 7 Ferris Lane
Sydney NSW 2000
Main Tel 02 9364 2710
Direct Tel 02 8472 3159
Email paul@qvlegal.com.au
www.qvlegal.com.au

Letterhead design should include logo plus:
Level 9, 7 Ferris Lane
Sydney NSW 2000
Tel 02 8472 3159
www.qvlegal.com.au

```html
<!DOCTYPE html>
<html lang="en">
<head>
<meta charset="utf-8">
<title>Quayvale Legal – Business Card</title>
<link rel="stylesheet" href="https://fonts.googleapis.com/css2?family=Open+Sans:wght@400;600;700&display=swap">
<style>
  :root {
    --backdrop: #c7cbcb;
    --card: #f4f3f0;
    --navy: #17203f;
    --ink: #2a2a2a;
    --muted: #5b5b5b;
  }
  * { box-sizing: border-box; margin: 0; padding: 0; }
  html, body {
    width: 1200px;
    height: 824px;
    overflow: hidden;
    background: var(--backdrop);
    font-family: "Open Sans", Arial, sans-serif;
  }
  .sheet {
    width: 1200px;
    height: 824px;
    display: flex;
    align-items: center;
    justify-content: center;
    gap: 32px;
  }
  .card {
    width: 560px;
    height: 320px;
    background: var(--card);
    position: relative;
    box-shadow: 0 2px 6px rgba(0,0,0,0.12);
  }
  .wordmark {
    display: flex;
    flex-direction: column;
    align-items: center;
    gap: 14px;
  }
  .wordmark-square {
    width: 34px;
    height: 34px;
    background: var(--navy);
  }
  .wordmark-name {
    font-weight: 600;
    color: var(--navy);
    letter-spacing: 0.14em;
    text-transform: uppercase;
    white-space: nowrap;
  }
  /* Front */
  .card-front .wordmark {
    position: absolute;
    left: 34px;
    top: 92px;
    width: 230px;
  }
  .card-front .wordmark-name { font-size: 21px; }
  .contact {
    position: absolute;
    left: 292px;
    top: 100px;
    color: var(--muted);
    font-size: 12.5px;
    line-height: 1.35;
  }
  .contact-name {
    font-size: 25px;
    font-weight: 700;
    color: var(--navy);
    line-height: 1.05;
  }
  .contact-role {
    font-size: 16.5px;
    font-weight: 700;
    color: var(--ink);
    margin-bottom: 8px;
  }
  .contact-address { margin-bottom: 10px; }
  .contact-lines { margin-bottom: 8px; }
  .contact-web {
    font-weight: 600;
    color: var(--ink);
    font-size: 13px;
  }
  /* Back */
  .card-back {
    display: flex;
    align-items: center;
    justify-content: center;
  }
  .card-back .wordmark-name { font-size: 27px; }
</style>
</head>
<body>
  <main class="sheet">
    <section class="card card-front" aria-label="Card front">
      <div class="wordmark">
        <span class="wordmark-square"></span>
        <span class="wordmark-name">Quayvale Legal</span>
      </div>
      <div class="contact">
        <p class="contact-name">Paul Whitcombe</p>
        <p class="contact-role">Managing Partner</p>
        <p class="contact-address">Level 9, 7 Ferris Lane<br>Sydney NSW 2000</p>
        <p class="contact-lines">02 9364 2710 (Main)<br>02 8472 3159 (Direct)<br>paul@qvlegal.com.au</p>
        <p class="contact-web">www.qvlegal.com.au</p>
      </div>
    </section>
    <section class="card card-back" aria-label="Card back">
      <div class="wordmark">
        <span class="wordmark-square"></span>
        <span class="wordmark-name">Quayvale Legal</span>
      </div>
    </section>
  </main>
</body>
</html>
```